Exclusive Crestline Groomers Invite that connects barbers

I am looking for a general invitation to join a secret club of people that shave their head. I want it the size of a business card that I can hand out to people I see on the street. I want it to feel like a special exclulisve invite to a club that only they can be apart of and want to tell their friends about.

Target Market(s)

35-60 male

Industry/Entity Type

Hair

Contact Information for Business Card

I want it to look like an invite to a secret club that only people that shave their head can be apart of... I will hand it out to people that I think fir our demographic.

Font styles to use
Serif

Colors

Designer to choose colors to be used in the design.

Requirements
Must have
• A feel of exclusivity
• website address (www.crestlinegroomers.example)
• logo

```html
<!DOCTYPE html>
<html lang="en">
<head>
<meta charset="utf-8">
<title>Crestline Groomers — Business Card</title>
<link rel="stylesheet" href="https://fonts.googleapis.com/css2?family=Michroma&family=Roboto:wght@400;700&display=swap">
<style>
  :root {
    --stage: #3a3a3a;
    --card-dark: #141414;
    --card-dark-edge: #2a2a2a;
    --card-light: #ffffff;
    --ink: #1c1c1c;
    --ink-soft: #4a4a4a;
    --brand-light: #f2f2f2;
    --rule: #222222;
  }
  * { box-sizing: border-box; margin: 0; padding: 0; }
  html, body { width: 1200px; height: 896px; overflow: hidden; }
  body {
    background: var(--stage);
    display: flex;
    align-items: center;
    justify-content: center;
    gap: 40px;
    font-family: "Roboto", Arial, sans-serif;
  }
  .card {
    width: 540px;
    height: 309px;
    border-radius: 22px;
    position: relative;
    overflow: hidden;
  }

  /* Front */
  .card-front {
    background: linear-gradient(150deg, var(--card-dark-edge) 0%, var(--card-dark) 50%, #0c0c0c 100%);
    display: flex;
    flex-direction: column;
    align-items: center;
    justify-content: center;
    gap: 20px;
  }
  .brand-mark {
    border: 4px solid var(--brand-light);
    border-radius: 3px;
  }
  .card-front .brand-mark { width: 84px; height: 84px; }
  .brand-name {
    font-family: "Michroma", "Roboto", sans-serif;
    white-space: nowrap;
  }
  .card-front .brand-name {
    font-size: 29px;
    color: var(--brand-light);
  }

  /* Back */
  .card-back {
    background: var(--card-light);
    color: var(--ink);
    display: grid;
    grid-template-columns: 210px 1fr;
    align-items: center;
    padding: 0 30px 0 24px;
  }
  .back-brand {
    display: flex;
    flex-direction: column;
    align-items: center;
    justify-content: center;
    gap: 12px;
    height: 200px;
    padding-right: 18px;
    border-right: 2px solid var(--rule);
  }
  .back-brand .brand-mark {
    width: 92px; height: 92px;
    border-color: var(--ink);
  }
  .back-brand .brand-name {
    font-size: 12px;
    color: var(--ink);
  }
  .contact { padding-left: 26px; }
  .contact-name {
    font-weight: 700;
    font-size: 22px;
    letter-spacing: 1px;
    text-transform: uppercase;
    line-height: 1.1;
  }
  .contact-role {
    font-size: 13px;
    color: var(--ink-soft);
    margin: 3px 0 16px;
  }
  .contact-list { list-style: none; }
  .contact-list li {
    display: flex;
    align-items: flex-start;
    gap: 9px;
    font-size: 13px;
    line-height: 1.45;
    margin-bottom: 3px;
    white-space: nowrap;
  }
  .contact-list svg {
    width: 11px; height: 11px;
    margin-top: 3px;
    flex: none;
    fill: none;
    stroke: var(--ink);
    stroke-width: 1.6;
  }
  .contact-list .solid { fill: var(--ink); stroke: none; }
</style>
</head>
<body>
  <section class="card card-front">
    <div class="brand-mark"></div>
    <div class="brand-name">Crestline Groomers</div>
  </section>

  <section class="card card-back">
    <div class="back-brand">
      <div class="brand-mark"></div>
      <div class="brand-name">Crestline Groomers</div>
    </div>
    <div class="contact">
      <h1 class="contact-name">Marcus Hale</h1>
      <p class="contact-role">Founder</p>
      <ul class="contact-list">
        <li>
          <svg viewBox="0 0 12 12"><path class="solid" d="M6 11 C3 7 2 5.5 2 4.2 A4 4 0 0 1 10 4.2 C10 5.5 9 7 6 11Z"/></svg>
          <span>418 Alder Ave #120,<br>Fairview, CO 80000</span>
        </li>
        <li>
          <svg viewBox="0 0 12 12"><rect x="3" y="1" width="6" height="10" rx="1"/></svg>
          <span>555.014.2290</span>
        </li>
        <li>
          <svg viewBox="0 0 12 12"><path class="solid" d="M2 2 L4.5 2 L5.5 4.5 L4.2 5.5 A6 6 0 0 0 6.5 7.8 L7.5 6.5 L10 7.5 L10 10 A8 8 0 0 1 2 2Z"/></svg>
          <span>555-014-3817</span>
        </li>
        <li>
          <svg viewBox="0 0 12 12"><rect x="1" y="2.5" width="10" height="7"/><path d="M1 2.5 L6 6.5 L11 2.5"/></svg>
          <span>info@crestlinegroomers.example</span>
        </li>
        <li>
          <svg viewBox="0 0 12 12"><circle cx="6" cy="6" r="5"/><path d="M1 6 H11 M6 1 C3.5 3.5 3.5 8.5 6 11 M6 1 C8.5 3.5 8.5 8.5 6 11"/></svg>
          <span>www.crestlinegroomers.example</span>
        </li>
      </ul>
    </div>
  </section>
</body>
</html>
```